Realtor branding business card

modern, simple and self branding. Broker office logo needs to be used but not emphasized. Looking to brand myself

Target Market(s)

buyers, sellers and investors

Industry/Entity Type

Realtor

Contact Information for Business Card

Sample of my current business card on file

Requirements
Must have
• my website - tobiasmerrowkl.com
• Realtor logo
• Fair housing logo
Nice to have
• Colors from office logo but not a must
Should not have
• Do not want headshot

```html
<!DOCTYPE html>
<html lang="en">
<head>
<meta charset="utf-8">
<title>The Merrow Group – Business Card</title>
<link rel="stylesheet" href="https://fonts.googleapis.com/css2?family=Arimo:wght@400;700&display=swap">
<style>
  :root{
    --page:#e6e4e0;
    --card-light:#f4f4f3;
    --card-light-edge:#dcdcdb;
    --ink:#2b2b2b;
    --ink-soft:#5e5e5e;
    --accent:#c8202a;
    --skyline:#5c5d60;
    --back-top:#6f7175;
    --back-bottom:#45474a;
    --white:#ffffff;
  }
  *{box-sizing:border-box;margin:0;padding:0}
  html,body{width:800px;height:1200px;overflow:hidden}
  body{background:var(--page);font-family:"Arimo",Arial,sans-serif;position:relative}

  .card{position:absolute;border-radius:22px;overflow:hidden;box-shadow:0 10px 28px rgba(0,0,0,.22)}

  /* Front */
  .card-front{left:240px;top:50px;width:320px;height:560px;
    background:linear-gradient(160deg,var(--card-light),var(--card-light-edge));
    border-bottom:8px solid var(--accent)}
  .brand{text-align:center;margin-top:62px;font-size:30px;font-weight:700;line-height:1.1;color:var(--ink)}
  .rule{height:1px;background:var(--accent);opacity:.6;margin:14px 40px}
  .agent{text-align:center;margin-top:18px}
  .agent-name{font-size:19px;font-weight:700;color:var(--ink-soft);letter-spacing:.5px}
  .agent-title{font-size:13px;color:var(--accent);margin-top:2px}
  .contact{list-style:none;margin:18px 0 0 52px;font-size:14px;color:var(--ink)}
  .contact li{display:flex;align-items:center;gap:9px;margin:6px 0}
  .contact svg{width:14px;height:14px;flex:none}
  .address{margin:0 0 0 52px;font-size:14px;color:var(--ink);line-height:1.35}
  .skyline{position:absolute;left:0;bottom:0;width:100%;height:150px;
    background:linear-gradient(180deg,#6a6b6e,var(--skyline))}
  .badges{position:absolute;left:200px;bottom:100px;display:flex;gap:10px}
  .badge{width:30px;height:30px;background:var(--white);border:2px solid var(--ink)}
  .website{position:absolute;left:0;right:0;bottom:24px;text-align:center;color:var(--white);font-size:15px;letter-spacing:.5px}

  /* Back */
  .card-back{left:120px;top:680px;width:560px;height:320px;
    background:linear-gradient(160deg,var(--back-top),var(--back-bottom));
    display:flex;flex-direction:column;align-items:center;justify-content:center;color:var(--white)}
  .office{display:flex;align-items:center;gap:14px}
  .office-mark{width:28px;height:28px;background:var(--white)}
  .office-name{font-size:34px;font-weight:700;line-height:1}
  .office-web{margin-top:26px;font-size:14px;letter-spacing:5px}
</style>
</head>
<body>

<section class="card card-front">
  <header class="brand">The Merrow Group</header>
  <div class="rule"></div>

  <div class="agent">
    <div class="agent-name">TOBIAS MERROW, PA</div>
    <div class="agent-title">Realtor</div>
  </div>

  <ul class="contact">
    <li><svg viewBox="0 0 14 14"><rect x="3.5" y="1" width="7" height="12" rx="1.2" fill="none" stroke="#2b2b2b" stroke-width="1.4"/></svg>555.204.7781</li>
    <li><svg viewBox="0 0 14 14"><rect x="1" y="3" width="12" height="8" fill="none" stroke="#2b2b2b" stroke-width="1.4"/><path d="M1 3l6 5 6-5" fill="none" stroke="#2b2b2b" stroke-width="1.4"/></svg>merrowrealty@mailbox.com</li>
    <li><svg viewBox="0 0 14 14"><path d="M2 5c0-2 2-3 5-3s5 1 5 3l-2 1-1-2H5L4 6z" fill="#2b2b2b"/><rect x="3" y="7" width="8" height="5" rx="1" fill="#2b2b2b"/></svg>555.310.4400</li>
  </ul>
  <div class="rule"></div>
  <p class="address">48 Linden Crest Ave.<br>Harbor Springs, FL 30218</p>

  <div class="skyline" role="img" aria-label="City skyline silhouette"></div>
  <div class="badges">
    <span class="badge" role="img" aria-label="Fair housing badge"></span>
    <span class="badge" role="img" aria-label="Realtor badge"></span>
  </div>
  <div class="website">www.tobiasmerrowkl.com</div>
</section>

<section class="card card-back">
  <div class="office">
    <span class="office-mark"></span>
    <span class="office-name">Keystone Realty Group</span>
  </div>
  <div class="office-web">www.keystonerealtyfl.com</div>
</section>

</body>
</html>
```